VOMRA Pty Ltd Business Card

Looking for a simple yet eye-catching double-sided business card design using my company logo on one side and contact details on the other.

Target Market(s)

Government

Industry/Entity Type

Communication Systems Engineering

Contact Information for Business Card

VOMRA Pty Ltd

Requirements
Nice to have
• Would be great to have a QR code so details can be scanned into contacts

```html
<!DOCTYPE html>
<html lang="en">
<head>
<meta charset="utf-8">
<title>VOMRA Pty Ltd Business Card</title>
<link href="https://fonts.googleapis.com/css2?family=Arimo:wght@400;700&display=swap" rel="stylesheet">
<style>
  :root {
    --stage: #2b2d31;
    --navy: #13294b;
    --navy-deep: #0c1d38;
    --navy-light: #1e3a66;
    --white: #ffffff;
    --band-grey: #c9ced8;
    --text-soft: #d8deea;
  }
  * { margin: 0; padding: 0; box-sizing: border-box; }
  html, body { width: 1200px; height: 849px; overflow: hidden; }
  body {
    background: var(--stage);
    font-family: "Arimo", Arial, sans-serif;
    position: relative;
  }
  .card {
    position: absolute;
    left: 320px;
    width: 560px;
    height: 320px;
    border-radius: 26px;
    overflow: hidden;
    box-shadow: 0 14px 30px rgba(0,0,0,0.45);
  }
  /* Front side */
  .card--front {
    top: 72px;
    background: linear-gradient(120deg, var(--navy-light) 0%, var(--navy) 45%, var(--navy-deep) 100%);
    color: var(--white);
  }
  .front-brand {
    position: absolute;
    left: 60px;
    top: 140px;
    display: flex;
    align-items: center;
    gap: 12px;
  }
  .brand-dot {
    width: 22px; height: 22px;
    border-radius: 50%;
    background: currentColor;
    opacity: 1;
  }
  .brand-name {
    font-weight: 700;
    font-size: 34px;
    letter-spacing: 4px;
    line-height: 1;
  }
  .front-divider {
    position: absolute;
    left: 252px;
    top: 60px;
    width: 1px;
    height: 180px;
    background: rgba(255,255,255,0.55);
  }
  .front-copy {
    position: absolute;
    left: 272px;
    top: 66px;
    width: 270px;
  }
  .front-heading {
    font-weight: 700;
    font-size: 14.5px;
    letter-spacing: 0.6px;
    margin-bottom: 8px;
  }
  .front-body {
    font-size: 10.5px;
    line-height: 1.6;
    color: var(--text-soft);
    letter-spacing: 0.3px;
  }
  .front-body + .front-body { margin-top: 8px; }
  .front-rule {
    position: absolute;
    left: 0; right: 0;
    bottom: 34px;
    height: 1px;
    background: rgba(255,255,255,0.6);
  }
  /* Back side */
  .card--back {
    top: 458px;
    background: var(--white);
    color: var(--navy);
  }
  .back-brand {
    position: absolute;
    left: 0; right: 0;
    top: 60px;
    display: flex;
    justify-content: center;
    align-items: center;
    gap: 14px;
  }
  .back-brand .brand-name { font-size: 36px; }
  .band {
    position: absolute;
    left: 0; right: 0;
  }
  .band--grey { top: 142px; height: 16px; background: var(--band-grey); }
  .band--navy { top: 268px; height: 12px; background: var(--navy); }
  .contact {
    position: absolute;
    right: 34px;
    top: 186px;
    text-align: right;
    font-weight: 700;
    font-size: 12px;
    line-height: 1.9;
    letter-spacing: 0.4px;
  }
</style>
</head>
<body>
  <section class="card card--front" aria-label="Business card front">
    <div class="front-brand">
      <span class="brand-dot"></span>
      <span class="brand-name">VOMRA</span>
    </div>
    <div class="front-divider"></div>
    <div class="front-copy">
      <h2 class="front-heading">SYSTEM INTEGRATION SOLUTIONS</h2>
      <p class="front-body">let solve your technical issues through<br>our knowledge<br>and experience of systems components<br>and engineering.</p>
      <p class="front-body">At VOMRA we strive to ensure your missioncritical<br>teams have reliable assured communications.</p>
    </div>
    <div class="front-rule"></div>
  </section>

  <section class="card card--back" aria-label="Business card back">
    <div class="back-brand">
      <span class="brand-dot"></span>
      <span class="brand-name">VOMRA</span>
    </div>
    <div class="band band--grey"></div>
    <div class="contact">
      <p>Email: admin@vomra.com.au</p>
      <p>Postal Address: 14- 16 Harbour Lane Millbrook NSW 2999 Australia</p>
    </div>
    <div class="band band--navy"></div>
  </section>
</body>
</html>
```